Business Card Design - ChoiceCraft

Looking for creative, modern design, two sided for ChoiceCraft that is consistent with color and feel of website www.choicecraftpro.net.
Updates

Back of card will be used to promote products or have a quote revolving around decisions, change, leadership, innovation, creativity. Back should also have space to promote website, but optional to use the icon. Front of the card will need to use the icon and have standard place for name, job title, phone and email. We are not looking to put a mailing address or fax. Also want space to place a few words/phrase explaining what we do...such as individual growth and organizational development or tools, training, information...in addition, want the facebook icon small on the front somewhere as we are also on facebook.

Vector file uploaded of icon.

Target Market(s)

Professional coaching for individual growth and organizational development

Industry/Entity Type

Business

Requirements
Must have
• Icon...see attached.

```html
<!DOCTYPE html>
<html lang="en">
<head>
<meta charset="utf-8">
<title>ChoiceCraft Business Card</title>
<link href="https://fonts.googleapis.com/css2?family=Tinos:wght@400;700&family=Arimo:wght@400;700&display=swap" rel="stylesheet">
<style>
  :root {
    --backdrop: #b9bcbf;
    --card-white: #ffffff;
    --brand-blue: #2a7fc4;
    --navy: #2c3a8c;
    --sky: #3aa6e6;
    --deep-blue: #0f6db8;
    --silver: #8e949c;
    --ink: #2b2b2b;
    --rule: #9a9a9a;
  }
  * { margin: 0; padding: 0; box-sizing: border-box; }
  html, body { width: 1200px; height: 393px; overflow: hidden; }
  body { background: var(--backdrop); position: relative; font-family: "Tinos", "Times New Roman", serif; }

  .card {
    position: absolute;
    top: 39px;
    height: 309px;
    border-radius: 16px;
    overflow: hidden;
  }
  .card-front { left: 39px; width: 543px; background: var(--card-white); }
  .card-back {
    left: 621px; width: 539px; height: 307px;
    background: radial-gradient(ellipse at 55% 55%, #5cc0f2 0%, var(--sky) 35%, var(--deep-blue) 100%);
    font-family: "Arimo", Arial, sans-serif;
    color: #ffffff;
  }

  /* Front: brand lockup */
  .brand { position: absolute; left: 127px; top: 28px; display: flex; align-items: center; gap: 20px; }
  .brand-mark {
    width: 90px; height: 90px; border-radius: 50%;
    background: radial-gradient(circle at 40% 35%, #e4e8ee, #9aa4b0);
    border: 4px solid var(--brand-blue);
  }
  .brand-name { font-size: 24px; font-weight: 700; color: var(--brand-blue); letter-spacing: 0.3px; }

  .tagline {
    position: absolute; right: 255px; top: 148px;
    text-align: right; font-size: 13.5px; line-height: 14.5px; color: var(--ink);
  }
  .divider { position: absolute; left: 288px; top: 142px; width: 1px; height: 68px; background: var(--rule); }

  .contact { position: absolute; left: 298px; top: 144px; list-style: none; font-size: 13.5px; line-height: 15.5px; color: var(--ink); }
  .contact li { display: flex; align-items: center; gap: 6px; }
  .contact svg { width: 10px; height: 10px; flex: none; }
  .social-square { width: 9px; height: 9px; background: #3b5a9a; flex: none; }

  .swoosh { position: absolute; left: 0; bottom: 0; width: 543px; height: 100px; }

  .person { position: absolute; left: 348px; top: 248px; width: 160px; text-align: center; color: #ffffff; }
  .person-name { font-size: 20px; font-weight: 700; line-height: 22px; }
  .person-title { font-size: 14px; line-height: 20px; }

  /* Back: quotes */
  .quotes { position: absolute; left: 16px; top: 22px; list-style: none; }
  .quote { position: relative; padding-left: 37px; margin-bottom: 11.5px; }
  .quote-text { font-size: 13.5px; line-height: 21px; }
  .quote-text::before {
    content: "\201C"; position: absolute; left: 20px; top: -6px;
    font-family: "Tinos", serif; font-size: 24px; font-weight: 700;
  }
  .quote-text::after {
    content: "\201D"; font-family: "Tinos", serif; font-size: 24px; font-weight: 700;
    vertical-align: -9px; margin-left: 2px; line-height: 0;
  }
  .quote-author { font-size: 13.5px; font-weight: 700; line-height: 21px; }

  .back-mark {
    position: absolute; left: 365px; top: 165px; width: 102px; height: 102px; border-radius: 50%;
    border: 4px solid rgba(255,255,255,0.45);
    background: rgba(255,255,255,0.12);
    display: flex; align-items: center; justify-content: center;
  }
  .back-mark span { font-family: "Arimo", Arial, sans-serif; font-size: 13px; font-weight: 700; color: rgba(255,255,255,0.7); }
</style>
</head>
<body>

<section class="card card-front" aria-label="Card front">
  <div class="brand">
    <div class="brand-mark"></div>
    <span class="brand-name">ChoiceCraft</span>
  </div>

  <p class="tagline">Supporting individual growth<br>and organizational development<br>or tools, training, information</p>
  <div class="divider"></div>

  <ul class="contact">
    <li><svg viewBox="0 0 10 10"><path d="M2 1 L4 1 L4.6 3 L3.4 4 Q4.5 6 6 6.6 L7 5.4 L9 6 L9 8 Q8 9 6.5 8.6 Q2.5 7 1.4 3 Q1 1.6 2 1 Z" fill="#333"/></svg>123-456-789</li>
    <li><svg viewBox="0 0 10 10"><rect x="0.5" y="2" width="9" height="6.5" fill="#333"/><path d="M0.5 2 L5 5.5 L9.5 2" stroke="#fff" stroke-width="0.9" fill="none"/></svg>info@choicecraftpro.net</li>
    <li><svg viewBox="0 0 10 10"><circle cx="5" cy="5" r="4.3" fill="none" stroke="#333" stroke-width="1"/><ellipse cx="5" cy="5" rx="1.8" ry="4.3" fill="none" stroke="#333" stroke-width="0.8"/><line x1="0.7" y1="5" x2="9.3" y2="5" stroke="#333" stroke-width="0.8"/></svg>www.choicecraftpro.net</li>
    <li><span class="social-square"></span>/choicecraftpro</li>
  </ul>

  <svg class="swoosh" viewBox="0 0 543 100" preserveAspectRatio="none" aria-hidden="true">
    <defs>
      <linearGradient id="blueFill" x1="0" y1="0" x2="1" y2="0">
        <stop offset="0" stop-color="#1f74bf"/>
        <stop offset="0.55" stop-color="#4bb5ef"/>
        <stop offset="1" stop-color="#1566b3"/>
      </linearGradient>
      <linearGradient id="silverFill" x1="0" y1="0" x2="1" y2="0">
        <stop offset="0" stop-color="#5e646c"/>
        <stop offset="0.5" stop-color="#d8dce0"/>
        <stop offset="1" stop-color="#ffffff"/>
      </linearGradient>
    </defs>
    <path d="M0 48 Q150 30 300 40 Q430 48 543 20 L543 100 L0 100 Z" fill="#2c3a8c"/>
    <path d="M0 56 Q150 40 300 48 Q430 56 543 28 L543 100 L0 100 Z" fill="#ffffff"/>
    <path d="M0 64 Q160 52 330 66 L330 100 L0 100 Z" fill="url(#silverFill)"/>
    <path d="M0 100 Q180 90 300 62 Q420 36 543 32 L543 100 Z" fill="url(#blueFill)"/>
  </svg>

  <div class="person">
    <p class="person-name">Your Name</p>
    <p class="person-title">Title</p>
  </div>
</section>

<section class="card card-back" aria-label="Card back">
  <ul class="quotes">
    <li class="quote"><p class="quote-text">Try not to become a man of success, but rather a man of value.</p><p class="quote-author">- Arthur Ellison</p></li>
    <li class="quote"><p class="quote-text">The only constant is change.</p><p class="quote-author">- Helion Varos</p></li>
    <li class="quote"><p class="quote-text">We are what we repeatedly do. Excellence is not an act, it is a habit.</p><p class="quote-author">- Aristeas Moren</p></li>
    <li class="quote"><p class="quote-text">Simplicity is the ultimate sophistication.</p><p class="quote-author">- Lorenzo Devani</p></li>
    <li class="quote"><p class="quote-text">Life is not fair - get used to it.</p><p class="quote-author">- Ben Garrow</p></li>
  </ul>
  <div class="back-mark"><span>ChoiceCraft</span></div>
</section>

</body>
</html>
```